Grey Fennel Medical Website to make connecting and communicating easier

To create a unique, user-friendly, professional website for patients and professionals to access education/ information, forms, appointments, contact details, and data about us, and for us to have the capacity to link to various cloud-based platforms.
To use the logo design and colour scheme we have just sourced.

WEBSITE to be eye catching, Inspiring and alluring
- efficient and logical
- professional and trustworthy appearance
- health focus "living health matters"
- user friendly
- ability to link with cloud-based software and video conferencing tools/ telehealth
- colours- black/ white teal and ?silver

PAGES:
page 1 - Our clinic and staff, services offered, contact us- address/ map / contact details- social media connections
page 2- patients and visitors - New patient forms to complete, news and patient informtion (educatinal)
page 3 - health professionals -referral forms, research and education
page 3- online appointments
page 4 - Quick links - partners, other services
page 5- privacy policy, disclaimer

HI, Could we please extend the deadline another 5 days, so sorry just struggling with my workload to be able to keep up and I am wanting to liaise more with the designer that I will choose. I am so happy with SketchHarbor and all the designers - thank you! Thank you so much!!

Target Market(s)

Patients - mostly over 60's so the website must be minimal clicks and simple to navigate
Professionals - for education and access forms

Industry/Entity Type

Health Care

Coding

Coded - Design and coding required

Number of Pages Required

5+ page

Font styles to use
Sans Serif
Script

Colors
33b8a4
86cfc6

Requirements
Must have
• WEBSITE to be eye catching, Inspiring and alluring
- efficient and logical
- user friendly

WEBSITE - professional and user friendly
- ability to link with cloud based software and videoconferencing/ telehealth
Nice to have
• clean and crisp presentation
happy for an innovative look
room to add more services and ability to link pages and resources
Should not have
• Please ensure the website is not:
clunky
difficult to navigate
common and cheap looking

```html
<!DOCTYPE html>
<html lang="en">
<head>
<meta charset="utf-8">
<title>Health Professionals – Grey Fennel Medical</title>
<link href="https://fonts.googleapis.com/css2?family=Michroma&family=Montserrat:ital,wght@0,400;0,500;0,600;0,700;1,400&display=swap" rel="stylesheet">
<style>
:root{
  --teal:#1a9484;
  --teal-bright:#33b8a4;
  --teal-soft:#86cfc6;
  --ink:#111;
  --text:#333;
  --muted:#777;
  --line:#cfcfcf;
  --panel:#f2f2f2;
  --white:#fff;
  --black:#000;
}
*{box-sizing:border-box;margin:0;padding:0}
html,body{width:1200px;height:3284px;overflow:hidden}
body{font-family:"Montserrat",sans-serif;color:var(--text);background:var(--white);position:relative}
.abs{position:absolute}
.display{font-family:"Michroma",sans-serif;font-weight:400;color:var(--ink);text-align:center;white-space:nowrap}

/* header */
.site-header{left:0;top:0;width:1200px;height:90px;background:var(--white)}
.brand{display:flex;align-items:center;gap:8px}
.brand-mark{width:16px;height:16px;border-radius:50%;background:var(--teal-bright)}
.brand-name{font-family:"Montserrat",sans-serif;font-weight:700;color:var(--teal-bright);font-size:13px;line-height:1.1;width:80px}
.site-header .brand{left:182px;top:26px}
.main-nav{left:498px;top:39px}
.main-nav a{position:absolute;top:0;white-space:nowrap;text-decoration:none;color:#444;font-size:16px}
.social{display:flex;gap:8px}
.social span{display:block;border-radius:50%;background:var(--teal-soft)}
.site-header .social{left:861px;top:32px}
.site-header .social span{width:33px;height:33px;opacity:.85}

/* hero */
.hero{left:0;top:90px;width:1200px;height:375px;background:var(--teal);overflow:hidden}
.hero h1{position:absolute;left:0;width:1200px;top:163px;font-size:39px;color:var(--white);font-family:"Michroma",sans-serif;font-weight:400;text-align:center;z-index:2;white-space:nowrap}
.hero-art-left{position:absolute;left:0;top:70px;width:330px;height:305px;background:linear-gradient(160deg,#b9c8f5,#6f86e6 70%,#2f3c8c)}
.hero-art-right{position:absolute;left:905px;top:75px;width:240px;height:300px;background:linear-gradient(180deg,#9fd6cf 0%,#e08a4a 60%,#b8473a)}

/* referral form */
.section-title{font-size:34px}
.rule{width:38px;height:3px;background:var(--teal-bright)}
.field{height:46px;border:1px solid var(--line);border-radius:23px;display:flex;align-items:center;padding-left:24px;gap:8px;font-size:13px;color:#444;background:var(--white)}
.field svg{width:15px;height:15px;fill:#555}
.field .caret{position:absolute;right:26px;top:19px;width:0;height:0;border-left:5px solid transparent;border-right:5px solid transparent;border-top:6px solid #444}
.textarea{height:187px;border:1px solid var(--line);border-radius:6px;padding:22px 0 0 24px;display:flex;gap:8px;align-items:flex-start;font-size:13px;color:#444}
.textarea svg{width:15px;height:15px;fill:#555}
.pill-btn{width:228px;height:48px;border-radius:24px;background:var(--teal-bright);color:var(--white);font-weight:600;font-size:17px;display:flex;align-items:center;justify-content:center}

/* blogs */
.blogs{left:0;top:1186px;width:1200px;height:1037px;background:var(--panel)}
.card{width:262px;height:352px;background:var(--white)}
.card-img{width:262px;height:186px}
.card-body{padding:26px 20px 0 23px}
.card-body h3{font-size:16px;font-weight:700;color:var(--ink);margin-bottom:8px;white-space:nowrap}
.card-body p{font-size:11.5px;line-height:19px;color:var(--muted);white-space:nowrap;letter-spacing:-.1px}
.read-more{margin-top:6px;font-size:12px;font-weight:700;color:var(--teal-bright);display:flex;align-items:center;gap:6px}
.read-more svg{width:14px;height:8px}

/* education */
.doc{left:232px;width:735px;height:135px;border:1px solid var(--line);background:var(--white)}
.pdf-icon{position:absolute;left:37px;top:22px;width:76px;height:92px}
.divider-v{position:absolute;top:52px;width:1px;height:32px;background:var(--line)}
.doc-text{position:absolute;left:175px;top:25px;width:345px}
.doc-date{font-size:12px;font-style:italic;color:var(--teal-bright);display:flex;align-items:center;gap:5px}
.doc-text h4{font-size:17px;font-weight:700;color:var(--ink);margin:8px 0 6px;white-space:nowrap}
.doc-text p{font-size:10px;line-height:16px;color:#666;white-space:nowrap}
.doc-btn{position:absolute;left:571px;width:125px;height:31px;border-radius:16px;color:var(--white);font-size:11px;font-weight:700;display:flex;align-items:center;justify-content:center}
.doc-btn.primary{top:28px;background:var(--teal-bright)}
.doc-btn.secondary{top:75px;background:var(--teal-soft)}

/* footer */
.site-footer{left:0;top:2915px;width:1200px;height:369px;background:var(--black);color:var(--white)}
.site-footer .brand{left:190px;top:100px}
.site-footer .brand-mark{width:22px;height:22px}
.site-footer .brand-name{font-size:17px;width:110px}
.lang{left:184px;top:203px;width:139px;height:33px;border:1px solid #fff;display:flex;align-items:center;padding-left:26px;gap:6px;font-size:11px}
.flag{width:12px;height:12px;border-radius:50%;background:linear-gradient(#c33 0 50%,#239 50%)}
.lang .caret{position:absolute;right:22px;top:14px;border-left:4px solid transparent;border-right:4px solid transparent;border-top:5px solid #fff}
.f-col h5{font-size:17px;font-weight:700;margin-bottom:10px}
.f-col .rule{width:20px;height:2px;margin-bottom:14px}
.f-col li{list-style:none;font-size:11px;line-height:22.5px}
.contact-row{display:flex;gap:12px;font-size:10px;line-height:14px;margin-bottom:14px}
.contact-row svg{width:12px;height:14px;fill:#fff;flex:none;margin-top:2px}
.contact-row b{font-weight:700;display:block}
.site-footer .social span{width:34px;height:34px;background:var(--teal-bright)}
.footer-line{left:184px;top:313px;width:832px;height:1px;background:#333}
.legal{top:335px;font-size:11px}
</style>
</head>
<body>

<header class="site-header abs">
  <div class="brand abs"><span class="brand-mark"></span><span class="brand-name">Grey Fennel Medical</span></div>
  <nav class="main-nav abs">
    <a style="left:0">Home</a><a style="left:86px">Staff</a><a style="left:160px">Services</a><a style="left:259px">Contact Us</a>
  </nav>
  <div class="social abs" aria-label="Social links"><span></span><span></span><span></span><span></span></div>
</header>

<section class="hero abs">
  <div class="hero-art-left" role="img" aria-label="Illustration of a doctor on a large screen with medical icons"></div>
  <div class="hero-art-right" role="img" aria-label="Illustration of a doctor with clipboard talking with a patient"></div>
  <h1>Health Professionals</h1>
</section>

<section class="referral">
  <h2 class="display section-title abs" style="left:0;width:1200px;top:532px">Health professional, Refer Here...</h2>
  <div class="rule abs" style="left:581px;top:594px"></div>

  <div class="field abs" style="left:232px;top:635px;width:357px"><svg viewBox="0 0 16 16"><circle cx="8" cy="4.5" r="3.5"/><path d="M1 16c0-4 3-6.5 7-6.5s7 2.5 7 6.5z"/></svg>First Name*</div>
  <div class="field abs" style="left:611px;top:635px;width:357px"><svg viewBox="0 0 16 16"><circle cx="8" cy="4.5" r="3.5"/><path d="M1 16c0-4 3-6.5 7-6.5s7 2.5 7 6.5z"/></svg>Last Name*</div>
  <div class="field abs" style="left:232px;top:704px;width:357px"><svg viewBox="0 0 16 16"><rect x="1" y="4" width="3" height="10"/><rect x="5" y="4" width="9" height="3"/><rect x="6" y="8" width="2" height="5"/></svg>Speciality*<span class="caret"></span></div>
  <div class="field abs" style="left:611px;top:704px;width:357px"><svg viewBox="0 0 16 16"><path d="M8 0a6 6 0 0 0-6 6c0 4.5 6 10 6 10s6-5.5 6-10a6 6 0 0 0-6-6zm0 8.5A2.5 2.5 0 1 1 8 3.5a2.5 2.5 0 0 1 0 5z"/></svg>Address*</div>
  <div class="field abs" style="left:232px;top:772px;width:357px"><svg viewBox="0 0 16 16"><path d="M4 0h8a1 1 0 0 1 1 1v14a1 1 0 0 1-1 1H4a1 1 0 0 1-1-1V1a1 1 0 0 1 1-1zm1 2v11h6V2z"/></svg>Phone Number*</div>
  <div class="field abs" style="left:611px;top:772px;width:357px"><svg viewBox="0 0 16 16"><path d="M0 3h16v10H0zm1.5 1.2L8 9l6.5-4.8V4h-13z"/></svg>Email Address*</div>
  <div class="textarea abs" style="left:232px;top:840px;width:736px"><svg viewBox="0 0 16 16"><path d="M1 2h10v7H5l-3 3V9H1z"/><path d="M12 5h3v7h-1v3l-3-3H6v-2h6z"/></svg>Tell us About doctor...</div>
  <div class="pill-btn abs" style="left:486px;top:1065px">See All Our Services</div>
</section>

<section class="blogs abs">
  <h2 class="display section-title abs" style="left:0;width:1200px;top:72px">Blogs For Health Professionals</h2>

  <article class="card abs" style="left:185px;top:148px"><div class="card-img" role="img" aria-label="Illustration of a family wearing face masks" style="background:linear-gradient(135deg,#cfdcf7,#a9bff0)"></div><div class="card-body"><h3>Lorem Ipsum Door Sit...</h3><p>Lorem ipsum dolor sit amet, consec-<br>tetur adipiscing elit, sed do eiusmod<br>tempor incididunt ut labore et...</p><div class="read-more">Read More <svg viewBox="0 0 14 8"><path d="M0 4h12M9 1l3 3-3 3" stroke="#33b8a4" stroke-width="1.4" fill="none"/></svg></div></div></article>
  <article class="card abs" style="left:469px;top:148px"><div class="card-img" role="img" aria-label="Illustration of office workers wearing face masks" style="background:linear-gradient(180deg,#a9dbe0,#3b4570)"></div><div class="card-body"><h3>Lorem Ipsum Door Sit...</h3><p>Lorem ipsum dolor sit amet, consec-<br>tetur adipiscing elit, sed do eiusmod<br>tempor incididunt ut labore et...</p><div class="read-more">Read More <svg viewBox="0 0 14 8"><path d="M0 4h12M9 1l3 3-3 3" stroke="#33b8a4" stroke-width="1.4" fill="none"/></svg></div></div></article>
  <article class="card abs" style="left:754px;top:148px"><div class="card-img" role="img" aria-label="Illustration of surgeons in an operating room" style="background:linear-gradient(180deg,#eef2fb,#c9d5ef)"></div><div class="card-body"><h3>Lorem Ipsum Door Sit...</h3><p>Lorem ipsum dolor sit amet, consec-<br>tetur adipiscing elit, sed do eiusmod<br>tempor incididunt ut labore et...</p><div class="read-more">Read More <svg viewBox="0 0 14 8"><path d="M0 4h12M9 1l3 3-3 3" stroke="#33b8a4" stroke-width="1.4" fill="none"/></svg></div></div></article>

  <article class="card abs" style="left:185px;top:524px"><div class="card-img" role="img" aria-label="Medical illustration of a heart with a heartbeat line" style="background:linear-gradient(135deg,#8fe0e6,#c9f0f2)"></div><div class="card-body"><h3>Lorem Ipsum Door Sit...</h3><p>Lorem ipsum dolor sit amet, consec-<br>tetur adipiscing elit, sed do eiusmod<br>tempor incididunt ut labore et...</p><div class="read-more">Read More <svg viewBox="0 0 14 8"><path d="M0 4h12M9 1l3 3-3 3" stroke="#33b8a4" stroke-width="1.4" fill="none"/></svg></div></div></article>
  <article class="card abs" style="left:469px;top:524px"><div class="card-img" role="img" aria-label="Illustration of pharmacists with medicines" style="background:linear-gradient(180deg,#f3f4fb,#dfe3f5)"></div><div class="card-body"><h3>Lorem Ipsum Door Sit...</h3><p>Lorem ipsum dolor sit amet, consec-<br>tetur adipiscing elit, sed do eiusmod<br>tempor incididunt ut labore et...</p><div class="read-more">Read More <svg viewBox="0 0 14 8"><path d="M0 4h12M9 1l3 3-3 3" stroke="#33b8a4" stroke-width="1.4" fill="none"/></svg></div></div></article>
  <article class="card abs" style="left:754px;top:524px"><div class="card-img" role="img" aria-label="Illustration of a doctor presenting a medical chart" style="background:linear-gradient(135deg,#dfe6fb,#b8c8f3)"></div><div class="card-body"><h3>Lorem Ipsum Door Sit...</h3><p>Lorem ipsum dolor sit amet, consec-<br>tetur adipiscing elit, sed do eiusmod<br>tempor incididunt ut labore et...</p><div class="read-more">Read More <svg viewBox="0 0 14 8"><path d="M0 4h12M9 1l3 3-3 3" stroke="#33b8a4" stroke-width="1.4" fill="none"/></svg></div></div></article>

  <div class="pill-btn abs" style="left:486px;top:915px">See All Our Services</div>
</section>

<section class="education">
  <h2 class="display section-title abs" style="left:0;width:1200px;top:2290px">Educational Content</h2>
  <div class="rule abs" style="left:581px;top:2345px"></div>

  <article class="doc abs" style="top:2387px">
    <svg class="pdf-icon" viewBox="0 0 76 92"><path d="M4 4h50l18 18v66H4z" fill="#fff" stroke="#e3262b" stroke-width="4" stroke-linejoin="round"/><text x="38" y="76" font-family="Montserrat,sans-serif" font-size="18" font-weight="600" fill="#111" text-anchor="middle">PDF</text></svg>
    <span class="divider-v" style="left:142px"></span>
    <div class="doc-text"><div class="doc-date"><svg width="13" height="12" viewBox="0 0 13 12"><rect x="0.5" y="1.5" width="12" height="10" fill="none" stroke="#33b8a4"/><path d="M0.5 4.5h12" stroke="#33b8a4"/></svg>Wed, 11 Nov 2020</div><h4>Lorem ipsum carrots, enhanced...</h4><p>Lorem ipsum carrots, enhanced undergraduate developer, but<br>they do occaecat time and vitality, such...</p></div>
    <span class="divider-v" style="left:539px"></span>
    <div class="doc-btn primary">Read More</div><div class="doc-btn secondary">Download Pdf</div>
  </article>
  <article class="doc abs" style="top:2545px">
    <svg class="pdf-icon" viewBox="0 0 76 92"><path d="M4 4h50l18 18v66H4z" fill="#fff" stroke="#e3262b" stroke-width="4" stroke-linejoin="round"/><text x="38" y="76" font-family="Montserrat,sans-serif" font-size="18" font-weight="600" fill="#111" text-anchor="middle">PDF</text></svg>
    <span class="divider-v" style="left:142px"></span>
    <div class="doc-text"><div class="doc-date"><svg width="13" height="12" viewBox="0 0 13 12"><rect x="0.5" y="1.5" width="12" height="10" fill="none" stroke="#33b8a4"/><path d="M0.5 4.5h12" stroke="#33b8a4"/></svg>Wed, 11 Nov 2020</div><h4>Lorem ipsum carrots, enhanced...</h4><p>Lorem ipsum carrots, enhanced undergraduate developer, but<br>they do occaecat time and vitality, such...</p></div>
    <span class="divider-v" style="left:539px"></span>
    <div class="doc-btn primary">Read More</div><div class="doc-btn secondary">Download Pdf</div>
  </article>
  <article class="doc abs" style="top:2705px">
    <svg class="pdf-icon" viewBox="0 0 76 92"><path d="M4 4h50l18 18v66H4z" fill="#fff" stroke="#e3262b" stroke-width="4" stroke-linejoin="round"/><text x="38" y="76" font-family="Montserrat,sans-serif" font-size="18" font-weight="600" fill="#111" text-anchor="middle">PDF</text></svg>
    <span class="divider-v" style="left:142px"></span>
    <div class="doc-text"><div class="doc-date"><svg width="13" height="12" viewBox="0 0 13 12"><rect x="0.5" y="1.5" width="12" height="10" fill="none" stroke="#33b8a4"/><path d="M0.5 4.5h12" stroke="#33b8a4"/></svg>Wed, 11 Nov 2020</div><h4>Lorem ipsum carrots, enhanced...</h4><p>Lorem ipsum carrots, enhanced undergraduate developer, but<br>they do occaecat time and vitality, such...</p></div>
    <span class="divider-v" style="left:539px"></span>
    <div class="doc-btn primary">Read More</div><div class="doc-btn secondary">Download Pdf</div>
  </article>
</section>

<footer class="site-footer abs">
  <div class="brand abs"><span class="brand-mark"></span><span class="brand-name">Grey Fennel Medical</span></div>
  <div class="lang abs"><span class="flag"></span>English<span class="caret"></span></div>

  <div class="f-col abs" style="left:390px;top:72px">
    <h5>Quick Links</h5><div class="rule"></div>
    <ul><li>Home</li><li>Staff</li><li>Services</li><li>Contact Us</li><li>Patients</li><li>Health Professionals</li></ul>
  </div>
  <div class="f-col abs" style="left:559px;top:72px;width:200px">
    <h5>Contact Us</h5><div class="rule"></div>
    <div class="contact-row"><svg viewBox="0 0 12 14"><path d="M6 0a4.5 4.5 0 0 0-4.5 4.5C1.5 8 6 14 6 14s4.5-6 4.5-9.5A4.5 4.5 0 0 0 6 0zm0 6.3a1.8 1.8 0 1 1 0-3.6 1.8 1.8 0 0 1 0 3.6z"/></svg><span>Grey Fennel Medical</span></div>
    <div class="contact-row"><svg viewBox="0 0 12 14"><path d="M3 0h6a1 1 0 0 1 1 1v12a1 1 0 0 1-1 1H3a1 1 0 0 1-1-1V1a1 1 0 0 1 1-1zm.5 1.5v9.5h5V1.5z"/></svg><span><b>Call Us:</b>02 5550 1847</span></div>
    <div class="contact-row"><svg viewBox="0 0 12 14"><path d="M0 3h12v8H0zm1 1l5 3.6L11 4z"/></svg><span><b>Email.Us:</b>hello@greyfennelmedical.com</span></div>
  </div>
  <div class="f-col abs" style="left:773px;top:75px">
    <h5>Get Social</h5><div class="rule"></div>
    <div class="social" style="gap:9px" aria-label="Social links"><span></span><span></span><span></span><span></span></div>
  </div>

  <div class="footer-line abs"></div>
  <div class="legal abs" style="left:184px">Copyright © Grey Fennel Medical 2020. All right Reserved</div>
  <div class="legal abs" style="left:874px">Privacy Policy, Disclaimer</div>
</footer>

</body>
</html>
```